Medical Marihuana Ziplock Bag Mockup Design

We seek skilled and professional designer for medical marihuana ziplock bag packaging design. We need a modern, minimal, clean Design with the name productname: Plomu - Endproduct will be a ziplock bag (see attachment) samples.
Product may but must not contain a cannabis leaf in Design7Logo

Target Market(s)

young audience

Industry/Entity Type

Medical

Logo Text

P L O M U

Font styles to use
Serif
Sans Serif

Colors
9bcb3c
abd037
cadf82
ffc214
fece3e
fee18a
6b449b
886aae
b8a6cd

Requirements
Nice to have
• Can but must not contain a minimal cannabis leaf as abstract sign

```html
<!DOCTYPE html>
<html lang="de">
<head>
<meta charset="utf-8">
<title>Plomu – Schweizer Hanf 3g</title>
<link rel="stylesheet" href="https://fonts.googleapis.com/css2?family=Arimo:wght@700&family=Cormorant+Garamond:wght@500&family=Zilla+Slab:wght@600;700&family=Varela+Round&display=swap">
<style>
  :root {
    --green-top: #6a9a40;
    --green-logo: #6b9b3f;
    --green-dark: #2e5428;
    --green-light: #7db548;
    --green-pill: #86c24a;
    --green-sub: #9bcb3c;
    --leaf-light: #cadf82;
    --white: #ffffff;
    --black: #000000;
    --silver: #d9dadc;
  }
  html, body {
    margin: 0;
    padding: 0;
    overflow: hidden;
  }
  body {
    width: 901px;
    height: 1200px;
  }
  .pack {
    position: relative;
    width: 901px;
    height: 1200px;
    overflow: hidden;
    background: var(--silver);
  }
  .top-band {
    position: absolute;
    left: 0; top: 0;
    width: 901px; height: 52px;
    background: var(--green-top);
  }
  .header {
    position: absolute;
    left: 0; top: 52px;
    width: 901px; height: 355px;
    background: linear-gradient(180deg, var(--white) 0%, var(--white) 55%, #dcdddf 100%);
  }
  .dark-band {
    position: absolute;
    left: 0; top: 407px;
    width: 901px; height: 104px;
    background: var(--green-dark);
  }
  .leaf-art {
    position: absolute;
    left: 8px; top: 193px;
    width: 306px; height: 294px;
    border-radius: 50% 50% 40% 40%;
    background: radial-gradient(ellipse at 55% 65%, rgba(202,223,130,0.75) 0%, rgba(179,211,106,0.45) 40%, rgba(179,211,106,0) 70%);
  }
  .age {
    position: absolute;
    right: 24px; top: 74px;
    font-family: "Varela Round", sans-serif;
    font-size: 40px;
    color: var(--green-logo);
    line-height: 1;
  }
  .brand {
    position: absolute;
    left: 134px; top: 136px;
    font-family: "Cormorant Garamond", serif;
    font-weight: 500;
    font-size: 185px;
    line-height: 1;
    letter-spacing: -2px;
    color: var(--green-logo);
    margin: 0;
  }
  .claim {
    position: absolute;
    left: 191px; top: 374px;
    width: 518px; height: 69px;
    border-radius: 35px;
    background: var(--green-pill);
    box-shadow: 0 3px 6px rgba(0,0,0,0.25);
    display: flex;
    align-items: center;
    justify-content: center;
    font-family: "Zilla Slab", serif;
    font-weight: 700;
    font-size: 46px;
    color: var(--white);
  }
  .subline {
    position: absolute;
    left: 153px; top: 462px;
    font-family: "Zilla Slab", serif;
    font-weight: 600;
    font-size: 31px;
    letter-spacing: 0.6px;
    color: var(--green-sub);
    line-height: 1.2;
    margin: 0;
    white-space: nowrap;
  }
  .divider {
    position: absolute;
    left: 0; top: 511px;
    width: 901px; height: 4px;
    background: linear-gradient(90deg, var(--white), var(--silver), var(--white));
  }
  .body-area {
    position: absolute;
    left: 0; top: 515px;
    width: 901px; height: 685px;
    background: linear-gradient(180deg, var(--green-light) 0%, #5d9a3c 25%, #3f7232 60%, var(--green-dark) 100%);
  }
  .warning {
    position: absolute;
    left: 51px; top: 519px;
    width: 772px; height: 554px;
    border: 13px solid var(--black);
    background: var(--white);
    display: flex;
    flex-direction: column;
    justify-content: center;
    align-items: center;
    gap: 20px;
    font-family: "Arimo", sans-serif;
    font-weight: 700;
    font-size: 46px;
    line-height: 56px;
    color: var(--black);
    text-align: center;
  }
  .warning p {
    margin: 0;
  }
  .weight {
    position: absolute;
    left: 52px; top: 1108px;
    font-family: "Varela Round", sans-serif;
    color: var(--white);
    line-height: 1;
  }
  .weight .num { font-size: 64px; }
  .weight .unit { font-size: 44px; }
</style>
</head>
<body>
  <div class="pack">
    <div class="top-band"></div>
    <div class="header"></div>
    <div class="dark-band"></div>
    <div class="leaf-art" role="img" aria-label="Light green hemp leaf illustration"></div>
    <div class="age">18+</div>
    <h1 class="brand">PLOMU</h1>
    <div class="claim">100% Schweizer Hanf</div>
    <p class="subline">Product auf pflanzlicher Basis ohne Tabak</p>
    <div class="divider"></div>
    <div class="body-area"></div>
    <div class="warning">
      <p>Rauchen fügt Ihnen und den<br>Menschen in Ihrer Umgebung<br>erheblichen Schaden zu.</p>
      <p>Fumer nuit gravement à votre<br>santé et à celle de votre<br>entourage.</p>
      <p>Il fumo danneggia gravemente<br>te e chi ti sta intorno.</p>
    </div>
    <div class="weight"><span class="num">3</span><span class="unit">g</span></div>
  </div>
</body>
</html>
```